Letterhead and matching envelope design for a dental office

We need a new stationary design, letterhead and envelope #10, for a dental office in Denver area. We are called Bright Harbor Dental. We want a simple and minimalistic design but not a boring design. I wish to have one good point that makes it look professional. I have attached our logo. Feel free to use either one. I want the design for letterhead and envelope look like a "matching pair" but not look the same. The envelope doesn't have to be white and it will have an address window on bottom left.

Target Market(s)

everyone who visits dentist (adults)

Industry/Entity Type

Dental

Font styles to use
Other font styles liked:
• close to font on logo or something that matches well

Requirements
Must have
• professional
• simple, minimalistic
• unique point that stands out
Nice to have
• matching but not same design for letterhead and envelope
Should not have
• not look like all the other boring designs
• no flowery, distracting feats

```html
<!DOCTYPE html>
<html lang="en">
<head>
<meta charset="utf-8">
<title>Bright Harbor Dental — Envelope #10</title>
<link rel="stylesheet" href="https://fonts.googleapis.com/css2?family=Source+Sans+3:wght@400;600&display=swap">
<style>
  :root {
    --backdrop: #ebebeb;
    --paper: #ffffff;
    --brand-green: #3bb54a;
    --soft-green: #b6e0b9;
    --ink: #1f1f1f;
    --shadow: rgba(0, 0, 0, 0.14);
  }
  html, body {
    margin: 0;
    width: 1200px;
    height: 795px;
    overflow: hidden;
    background: var(--backdrop);
    font-family: "Source Sans 3", Arial, sans-serif;
  }
  .stage {
    position: relative;
    width: 1200px;
    height: 795px;
  }
  .envelope {
    position: absolute;
    width: 620px;
    height: 270px;
    background: var(--paper);
    box-shadow: 0 6px 18px var(--shadow);
    overflow: hidden;
  }
  .envelope--front { left: 80px; top: 405px; }
  .envelope--back  { left: 500px; top: 95px; }
  .envelope__art {
    position: absolute;
    inset: 0;
    width: 100%;
    height: 100%;
  }
  .brand {
    position: absolute;
    display: flex;
    align-items: center;
    gap: 7px;
    font-weight: 600;
    font-size: 13px;
    letter-spacing: 0.14em;
    text-transform: uppercase;
    color: var(--brand-green);
  }
  .brand__dot {
    width: 10px;
    height: 10px;
    border-radius: 50%;
    background: var(--brand-green);
  }
  .envelope--front .brand { left: 28px; top: 28px; }
  .envelope--back .brand {
    left: 50%;
    top: 70px;
    transform: translateX(-50%);
    color: var(--paper);
  }
  .envelope--back .brand__dot { background: var(--paper); }
  .return-address {
    position: absolute;
    left: 402px;
    top: 98px;
    margin: 0;
    font-style: normal;
    font-size: 12.5px;
    line-height: 1.32;
    color: var(--ink);
  }
  .contact-line {
    display: flex;
    align-items: center;
    gap: 5px;
  }
  .contact-icon {
    width: 11px;
    height: 11px;
    flex: none;
  }
  .leaf-placeholder {
    position: absolute;
    left: 218px;
    top: 170px;
    width: 64px;
    height: 38px;
    border-radius: 6px;
    background: linear-gradient(135deg, var(--brand-green), #5cc46a);
  }
</style>
</head>
<body>
<main class="stage">

  <section class="envelope envelope--back" aria-label="Envelope back">
    <svg class="envelope__art" viewBox="0 0 620 270" aria-hidden="true">
      <path fill="var(--brand-green)"
            d="M0,0 H620 V40 Q620,62 598,70 L330,176 Q310,184 290,176 L0,64 Z"/>
      <path fill="var(--paper)"
            d="M0,0 H620 V4 L310,124 L0,18 Z" opacity="0"/>
    </svg>
    <div class="brand"><span class="brand__dot"></span>Bright Harbor Dental</div>
  </section>

  <section class="envelope envelope--front" aria-label="Envelope front">
    <svg class="envelope__art" viewBox="0 0 620 270" aria-hidden="true">
      <path fill="var(--soft-green)" d="M0,72 C140,138 330,220 620,236 L620,270 L0,270 Z"/>
      <path fill="var(--paper)"      d="M0,84 C140,148 330,228 620,244 L620,270 L0,270 Z"/>
      <path fill="var(--brand-green)" d="M0,92 C140,156 330,234 620,250 L620,270 L0,270 Z"/>
    </svg>

    <div class="brand"><span class="brand__dot"></span>Bright Harbor Dental</div>

    <div class="leaf-placeholder" role="img" aria-label="Green leaf sprig decoration"></div>

    <address class="return-address">
      <div>4821 Maple Crest Blvd,</div>
      <div>Suite 210 Lakewood, CO 80226</div>
      <div class="contact-line">
        <svg class="contact-icon" viewBox="0 0 12 12" aria-hidden="true">
          <circle cx="6" cy="6" r="6" fill="var(--brand-green)"/>
          <path d="M4,3 L5,3 L5.6,4.6 L4.9,5.2 Q5.6,6.6 6.8,7.1 L7.4,6.4 L9,7 L9,8 Q6,9 3.5,5 Z" fill="#fff"/>
        </svg>
        720-555-0142
      </div>
      <div class="contact-line">
        <svg class="contact-icon" viewBox="0 0 12 12" aria-hidden="true">
          <circle cx="6" cy="6" r="6" fill="var(--brand-green)"/>
          <rect x="3" y="4" width="6" height="4.2" fill="none" stroke="#fff" stroke-width="0.9"/>
          <path d="M3,4 L6,6.4 L9,4" fill="none" stroke="#fff" stroke-width="0.9"/>
        </svg>
        info@brightharbordental.com
      </div>
      <div class="contact-line">
        <svg class="contact-icon" viewBox="0 0 12 12" aria-hidden="true">
          <circle cx="6" cy="6" r="6" fill="var(--brand-green)"/>
          <circle cx="6" cy="6" r="3.2" fill="none" stroke="#fff" stroke-width="0.8"/>
          <path d="M2.8,6 H9.2 M6,2.8 V9.2" stroke="#fff" stroke-width="0.7"/>
        </svg>
        www.brightharbordental.com
      </div>
    </address>
  </section>

</main>
</body>
</html>
```